New business stationairy

I need paper with header and footer and business cards.
I am a Ltd Company and my main field of expertise is QA/QC inspection in the Oil and Gas Industry. I will need all contact detail inserted and a footer with registration number and bank details etc

```html
<!DOCTYPE html>
<html lang="en">
<head>
<meta charset="utf-8">
<title>Halden Verification Services Ltd – Stationery</title>
<link rel="stylesheet" href="https://fonts.googleapis.com/css2?family=Fira+Sans:wght@400;600;700;800&display=swap">
<style>
  :root {
    --navy: #1f1d52;
    --stage: #6b6c70;
    --silver: #bcbdc0;
    --band-grey: #b4b5b8;
    --paper: #ffffff;
    --ink: #1f1d52;
    --muted: #4a4a5e;
  }
  * { margin: 0; padding: 0; box-sizing: border-box; }
  html, body { width: 1200px; height: 1089px; overflow: hidden; }
  body {
    position: relative;
    background: var(--stage);
    font-family: "Fira Sans", Arial, sans-serif;
    color: var(--ink);
  }
  .abs { position: absolute; }

  /* Letterhead */
  .letterhead {
    position: absolute; left: 436px; top: 22px; width: 738px; height: 1045px;
    background: var(--paper);
  }
  .letterhead .company-name {
    position: absolute; left: 59px; top: 36px;
    font-weight: 800; font-size: 25px; letter-spacing: 1.5px;
    color: var(--navy); text-transform: uppercase; white-space: nowrap;
  }
  .letterhead .contact-band { position: absolute; left: 39px; top: 65px; }
  .contact-band .item {
    position: absolute; top: 7px; font-size: 13px; font-weight: 600;
    color: #fff; white-space: nowrap; display: flex; align-items: center; gap: 8px;
  }
  .address-band { position: absolute; left: 0; top: 107px; }
  .address-label {
    position: absolute; left: 66px; top: 107px; font-size: 13px; font-weight: 700;
    color: var(--navy); line-height: 19px;
  }
  .address-lines {
    position: absolute; left: 67px; top: 131px; list-style: none;
    font-size: 12px; font-weight: 600; line-height: 16.8px; color: var(--navy);
  }
  .footer-band { position: absolute; left: 242px; top: 944px; }
  .registration {
    position: absolute; left: 282px; top: 946px; font-size: 12px; font-weight: 600;
    color: var(--navy); line-height: 22px;
  }
  .bank-info {
    position: absolute; left: 282px; top: 977px; font-size: 12px; font-weight: 600;
    color: var(--navy);
  }

  /* Business card front */
  .card-front {
    position: absolute; left: 49px; top: 272px; width: 423px; height: 240px;
    background: var(--navy); box-shadow: 4px 6px 10px rgba(0,0,0,.35);
  }
  .card-front .company-name {
    position: absolute; left: 13px; top: 110px;
    font-weight: 800; font-size: 38px; line-height: 41px; letter-spacing: 1px;
    color: #fff; text-transform: uppercase;
  }

  /* Business card back */
  .card-back {
    position: absolute; left: 49px; top: 532px; width: 423px; height: 238px;
    background: var(--silver); box-shadow: 4px 6px 10px rgba(0,0,0,.35);
  }
  .card-back .company-name {
    position: absolute; left: 52px; top: 28px;
    font-weight: 800; font-size: 15px; line-height: 17px; letter-spacing: .5px;
    color: var(--navy); text-transform: uppercase;
  }
  .card-back .address-lines {
    position: absolute; left: auto; right: 31px; top: 66px; text-align: right;
    font-size: 12.5px; font-weight: 400; line-height: 15.4px; color: var(--muted);
  }
  .card-back .band { position: absolute; left: 0; }
  .card-back .item {
    position: absolute; left: 55px; font-size: 13px; color: var(--navy);
    display: flex; align-items: center; gap: 7px; white-space: nowrap;
  }
</style>
</head>
<body>

  <section class="letterhead" aria-label="Letterhead">
    <div class="company-name">Halden Verification Services Ltd</div>

    <svg class="contact-band" width="555" height="33" viewBox="0 0 555 33" aria-hidden="true">
      <polygon points="0,0 555,0 537,33 0,33" fill="var(--navy)"/>
    </svg>
    <div class="contact-band" style="width:555px;height:33px;">
      <span class="item" style="left:28px">
        <svg width="8" height="13" viewBox="0 0 8 13"><rect x="0.8" y="0.8" width="6.4" height="11.4" rx="1.2" fill="none" stroke="#fff" stroke-width="1.4"/><circle cx="4" cy="10" r="0.8" fill="#fff"/></svg>
        07700 900418
      </span>
      <span class="item" style="left:142px">
        <svg width="12" height="9" viewBox="0 0 12 9"><rect width="12" height="9" fill="#fff"/><polyline points="0,0 6,5 12,0" fill="none" stroke="var(--navy)" stroke-width="1.2"/></svg>
        office@haldenvs.co.uk
      </span>
    </div>

    <svg class="address-band" width="126" height="19" viewBox="0 0 126 19" aria-hidden="true">
      <polygon points="0,0 126,0 118,19 0,19" fill="var(--band-grey)"/>
    </svg>
    <div class="address-label">Address:</div>
    <ul class="address-lines">
      <li>The Willows</li>
      <li>Mill Lane</li>
      <li>Ashcombe</li>
      <li>Brookfield</li>
      <li>Newton</li>
      <li>Wessex</li>
      <li>BN14 7QX</li>
    </ul>

    <svg class="footer-band" width="496" height="24" viewBox="0 0 496 24" aria-hidden="true">
      <polygon points="0,0 496,0 496,24 12,24" fill="var(--band-grey)"/>
    </svg>
    <div class="registration">Company Registration # <strong>8034721</strong></div>
    <div class="bank-info">Bank Information:</div>
  </section>

  <section class="card-front" aria-label="Business card front">
    <div class="company-name">Halden<br>Verification<br>Services Ltd</div>
  </section>

  <section class="card-back" aria-label="Business card back">
    <div class="company-name">Halden<br>Verification<br>Services Ltd</div>
    <ul class="address-lines">
      <li>The Willows</li>
      <li>Mill Lane</li>
      <li>Ashcombe</li>
      <li>Brookfield Newton</li>
      <li>Wessex</li>
      <li>BN14 7QX</li>
    </ul>

    <svg class="band" style="top:171px" width="267" height="20" viewBox="0 0 267 20" aria-hidden="true">
      <polygon points="0,0 267,0 256,20 0,20" fill="#fff"/>
    </svg>
    <svg class="band" style="top:195px" width="250" height="21" viewBox="0 0 250 21" aria-hidden="true">
      <polygon points="0,0 250,0 239,21 0,21" fill="#fff"/>
    </svg>
    <span class="item" style="top:172px">
      <svg width="11" height="8" viewBox="0 0 12 9"><rect width="12" height="9" fill="var(--navy)"/><polyline points="0,0 6,5 12,0" fill="none" stroke="#fff" stroke-width="1.2"/></svg>
      office@haldenvs.co.uk
    </span>
    <span class="item" style="top:197px">
      <svg width="8" height="13" viewBox="0 0 8 13"><rect x="0.8" y="0.8" width="6.4" height="11.4" rx="1.2" fill="none" stroke="var(--navy)" stroke-width="1.4"/><circle cx="4" cy="10" r="0.8" fill="var(--navy)"/></svg>
      07700 900418
    </span>
  </section>

</body>
</html>
```